KTWG application splash screen

We need a 1024x768 image for use as an application splash screen.
The image will be displayed full screen on an 10 inch industrial PC 1024x768 screen while our application is launching. The image should convey that the application is "Waiting for connection to Wi-Fi access point..." and include a graphic of the industrial PC connected to the access point via an Ethernet cable. A list of troubleshooting steps should be included at the bottom of the image. The troubleshooting steps should not be the main focus of the image and should be shown in a smaller font (but still readable at 1024x768 displayed on a 10 inch screen).
I will include a mock up of the general idea of what we are looking for as well as image files for the industrial PC, a screenshot of our application to show on the PC's screen and the AP.
For general look and feel and a sense of corporate branding please review our website https://marrowgatesoilworks.example/. The splash screen should reflect corporate branding.
Target Market(s)
Users of our application
Industry/Entity Type
Agriculture
Look and feel

```html
<!DOCTYPE html>
<html lang="en">
<head>
<meta charset="utf-8">
<title>KTWG Splash Screen – Waiting for Wi-Fi</title>
<link href="https://fonts.googleapis.com/css2?family=Poppins:wght@400;500;600&display=swap" rel="stylesheet">
<style>
  :root {
    --brand-green: #6ab277;
    --brand-green-dark: #5aa268;
    --surface: #ffffff;
    --backdrop: #e9e9e9;
    --ink: #2e2e2e;
    --ink-soft: #555555;
    --device-fill: #d9dcd8;
    --ap-fill: #f1f1f1;
  }
  * { box-sizing: border-box; margin: 0; padding: 0; }
  html, body {
    width: 1200px; height: 870px; overflow: hidden;
    background: var(--backdrop);
    font-family: "Poppins", sans-serif;
  }
  .splash {
    position: absolute; left: 40px; top: 15px;
    width: 1120px; height: 840px;
    background: var(--surface);
    overflow: hidden;
  }
  .hero {
    position: absolute; left: 0; top: 0;
    width: 1120px; height: 640px;
    background: var(--brand-green);
    border-radius: 0 0 48px 150px / 0 0 48px 90px;
  }
  .hero__title {
    position: absolute; left: 0; right: 0; top: 228px;
    text-align: center; color: var(--surface);
    font-weight: 500; font-size: 35px; letter-spacing: 0.2px;
  }
  .hero__diagram { position: absolute; left: 0; top: 0; }
  .status-footer {
    position: absolute; left: 90px; top: 665px; width: 820px;
    color: var(--ink);
  }
  .status-footer__label {
    display: inline-block;
    background: var(--brand-green); color: var(--surface);
    font-size: 12px; font-weight: 500;
    padding: 4px 14px; border-radius: 14px;
    margin-bottom: 10px;
  }
  .status-footer__item {
    display: flex; align-items: center; gap: 6px;
    font-size: 12.5px; line-height: 1.6;
  }
  .status-footer__icon {
    width: 12px; height: 12px; border-radius: 50%;
    border: 1.4px solid var(--brand-green);
    color: var(--brand-green); font-size: 8px; font-weight: 600;
    display: inline-flex; align-items: center; justify-content: center;
  }
  .status-footer__steps {
    list-style: disc; padding-left: 40px;
    font-size: 10.5px; line-height: 1.55; color: var(--ink-soft);
  }
  .brand-mark {
    position: absolute; right: 70px; top: 690px;
    display: flex; align-items: center; gap: 10px;
    color: var(--brand-green); font-weight: 600; font-size: 34px;
  }
  .brand-mark__dot {
    width: 16px; height: 16px; border-radius: 50%;
    background: var(--brand-green);
  }
</style>
</head>
<body>
  <main class="splash">
    <section class="hero">
      <h1 class="hero__title">Waiting for connection to Wi-Fi access point...</h1>
      <svg class="hero__diagram" width="1120" height="640" viewBox="0 0 1120 640">
        <path class="cable" d="M485 452 V470 H785 V448 H905 V430"
              fill="none" stroke="#ffffff" stroke-width="2" stroke-dasharray="7 5"/>
        <rect role="img" aria-label="Industrial PC showing the application bar chart"
              x="290" y="330" width="195" height="122" rx="8"
              fill="var(--device-fill)" stroke="#111" stroke-width="6"/>
        <rect role="img" aria-label="Wi-Fi access point with antennas"
              x="892" y="300" width="24" height="130" rx="6" fill="var(--ap-fill)"/>
      </svg>
    </section>

    <section class="status-footer">
      <span class="status-footer__label">Troubleshooting steps:</span>
      <p class="status-footer__item"><span class="status-footer__icon">!</span>This screen should only be visible for a short time on boot.</p>
      <p class="status-footer__item"><span class="status-footer__icon">!</span>If this screen stays visible for more than a minute:</p>
      <ul class="status-footer__steps">
        <li>Verify that the Wi-Fi Access Point (AP) powers up when this system does (indicated by a green light on the side of the AP).</li>
        <li>Check the Ethernet cable between this system and the AP for damage, and replace it if necessary.</li>
        <li>Power-cycle this system and wait for it to reboot fully.</li>
        <li>If the issue persists, contact KTWG support for further assistance.</li>
      </ul>
    </section>

    <div class="brand-mark"><span class="brand-mark__dot"></span>KTWG</div>
  </main>
</body>
</html>
```